Business Card Design for Software Development Company

I am looking for a business card design the incorporates my new logo (attached below).

Key information to include:
Name: Martin Quelbrook
Title: CEO
Email: martin@brightwellcivic.example
Phone: 555-218-9403
Website: www.brightwellcivic.example

NOTE: This design should be easy to edit so that we can order cards for different members of our team.

```html
<!DOCTYPE html>
<html lang="en">
<head>
<meta charset="utf-8">
<title>Brightwell Labs – Business Card</title>
<link href="https://fonts.googleapis.com/css2?family=Montserrat:wght@400;500;700&display=swap" rel="stylesheet">
<style>
  :root {
    --backdrop: #1a1a1a;
    --card-light: #f3f3f3;
    --card-dark: #202020;
    --ink: #222222;
    --teal: #17a894;
    --orange: #e8832a;
    --peach: #f2b27a;
    --dark-mark: #3c3c3c;
  }
  * { margin: 0; padding: 0; box-sizing: border-box; }
  html, body { width: 1200px; height: 1059px; overflow: hidden; }
  body {
    background: var(--backdrop);
    font-family: "Montserrat", sans-serif;
    position: relative;
  }
  .card {
    position: absolute;
    width: 690px;
    height: 392px;
    border-radius: 22px;
  }
  .card-front { left: 256px; top: 89px; background: var(--card-light); color: var(--ink); }
  .card-back { left: 254px; top: 547px; background: var(--card-dark); }

  .brand { position: absolute; }
  .brand-name {
    font-weight: 700;
    font-size: 46px;
    letter-spacing: -1px;
    line-height: 1;
    white-space: nowrap;
  }
  .brand-division {
    font-weight: 700;
    font-size: 6.5px;
    letter-spacing: 0.3px;
    text-align: right;
    margin-top: 4px;
  }
  .card-front .brand { left: 42px; top: 72px; }
  .card-front .brand-name { color: var(--ink); }
  .card-front .brand-division { color: var(--ink); }

  .person { position: absolute; left: 42px; top: 192px; }
  .person-name {
    font-weight: 700;
    font-size: 23px;
    letter-spacing: 0.2px;
    line-height: 1;
  }
  .person-name .first { color: var(--teal); }
  .person-name .last { color: var(--orange); }
  .person-title { font-size: 17px; font-weight: 400; margin-top: 7px; }
  .divider { width: 12px; height: 2px; background: var(--orange); margin-top: 13px; }

  .contacts { list-style: none; margin-top: 13px; }
  .contacts li {
    display: flex;
    align-items: center;
    gap: 8px;
    font-size: 17px;
    font-weight: 400;
    height: 31.5px;
  }
  .contacts svg { width: 14px; height: 14px; flex: none; }

  .card-back .brand {
    left: 50%;
    top: 170px;
    transform: translateX(-50%);
  }
  .card-back .brand-name { color: var(--dark-mark); font-size: 58px; }
  .card-back .brand-division { color: var(--dark-mark); font-size: 8px; }
</style>
</head>
<body>

<section class="card card-front">
  <div class="brand">
    <div class="brand-name">Brightwell Labs</div>
    <div class="brand-division">A DIVISION OF BRIGHTWELL CIVIC</div>
  </div>

  <div class="person">
    <div class="person-name"><span class="first">MARTIN</span> <span class="last">QUELBROOK</span></div>
    <div class="person-title">CEO</div>
    <div class="divider"></div>
    <ul class="contacts">
      <li>
        <svg viewBox="0 0 16 16" aria-hidden="true"><path fill="var(--peach)" d="M2 6c0-2 2.5-3 6-3s6 1 6 3v1h-3V5.8C10 5.4 9 5.3 8 5.3s-2 .1-3 .5V7H2zM4 8h8l1.5 5h-11z"/></svg>
        <span>555-218-9403</span>
      </li>
      <li>
        <svg viewBox="0 0 16 16" aria-hidden="true"><path fill="var(--teal)" d="M1 6l7-5 7 5v9H1zm2 1.2V13h10V7.2L8 10.5z"/></svg>
        <span>martin@brightwellcivic.example</span>
      </li>
      <li>
        <svg viewBox="0 0 16 16" aria-hidden="true"><circle cx="8" cy="8" r="7" fill="var(--orange)"/><path fill="var(--card-light)" d="M5 4c1.5 0 2.5 1 2 2.5S5 8 4.5 9.5 3 9 3 7.5 3.5 4 5 4zm5 5c1.5 0 2 1 1.5 2.5S10 13.5 9 13s-.5-4 1-4z"/></svg>
        <span>www.brightwellcivic.example</span>
      </li>
    </ul>
  </div>
</section>

<section class="card card-back">
  <div class="brand">
    <div class="brand-name">Brightwell Labs</div>
    <div class="brand-division">A DIVISION OF BRIGHTWELL CIVIC</div>
  </div>
</section>

</body>
</html>
```